Business Card Design

New business card design

Target Market(s)

Residential & Commercial Property Managers

Industry/Entity Type

Plumbing Services

Contact Information for Business Card

Name - Rowan Keddle, title - Director, Phone Number - 0431 286 517, email - rowan@tbk-plumbing.com.au, Company ABN - 73 215 904 386,

Font styles to use
Sans Serif

Colors
0054AA
0677BA
7BADD7
CADEEF
E8F1F8

```html
<!DOCTYPE html>
<html lang="en">
<head>
<meta charset="utf-8">
<title>TBK Plumbing Services – Business Card</title>
<link rel="stylesheet" href="https://fonts.googleapis.com/css2?family=Montserrat:wght@300;400;600;700&display=swap">
<style>
  :root {
    --stage: #2b2e33;
    --ink: #1f2327;
    --band: #1d2126;
    --paper: #ffffff;
    --sky: #27a9e1;
    --sky-deep: #1f97d3;
    --brand-blue: #0677ba;
    --mist: #e8f1f8;
    --text-dark: #2a2e33;
  }
  * { margin: 0; padding: 0; box-sizing: border-box; }
  html, body {
    width: 1200px; height: 900px; overflow: hidden;
    background: var(--stage);
    font-family: "Montserrat", Arial, sans-serif;
  }
  .canvas { position: relative; width: 1200px; height: 900px; }

  .card { position: absolute; border-radius: 28px; overflow: hidden; }

  /* Front of card */
  .card-front {
    left: 150px; top: 170px; width: 340px; height: 560px;
    background: var(--paper);
  }
  .front-band {
    height: 150px; background: var(--band);
    display: flex; align-items: center; justify-content: center;
  }
  .brand {
    text-align: center; font-weight: 300; color: #ffffff; line-height: 1;
  }
  .brand-name { font-size: 50px; letter-spacing: 2px; }
  .brand-tag { font-size: 10px; letter-spacing: 6px; margin-top: 8px; }

  .front-body { padding: 44px 34px 0; }
  .person-name { font-size: 26px; font-weight: 700; color: var(--sky); }
  .person-title { font-size: 15px; color: var(--text-dark); margin-top: 4px; }
  .contact-list { list-style: none; margin-top: 30px; }
  .contact-list li {
    display: flex; align-items: center; gap: 8px;
    font-size: 14px; color: var(--text-dark); margin-bottom: 10px;
  }
  .abn-label { color: var(--sky); }
  .contact-icon { width: 12px; height: 12px; flex: none; }
  .front-accent {
    position: absolute; right: -60px; bottom: -60px;
    width: 260px; height: 260px; border-radius: 50%;
    background: var(--mist);
  }

  /* Back of card */
  .card-back {
    left: 560px; top: 290px; width: 520px; height: 320px;
    background: linear-gradient(160deg, var(--sky) 0%, var(--sky-deep) 100%);
    display: flex; align-items: center; justify-content: center;
  }
  .card-back .brand-name { font-size: 96px; letter-spacing: 4px; }
  .card-back .brand-tag { font-size: 13px; letter-spacing: 12px; margin-top: 14px; }
</style>
</head>
<body>
<main class="canvas">

  <section class="card card-front" aria-label="Business card front">
    <div class="front-accent"></div>
    <header class="front-band">
      <div class="brand">
        <div class="brand-name">tbk</div>
        <div class="brand-tag">plumbing services</div>
      </div>
    </header>
    <div class="front-body" style="position:relative;">
      <h1 class="person-name">Rowan Keddle</h1>
      <p class="person-title">Director</p>
      <ul class="contact-list">
        <li><span><span class="abn-label">Company ABN</span> - 73 215 904 386</span></li>
        <li>
          <svg class="contact-icon" viewBox="0 0 24 24" aria-hidden="true"><path fill="#27a9e1" d="M6.6 10.8a15.1 15.1 0 0 0 6.6 6.6l2.2-2.2a1 1 0 0 1 1-.25 11.4 11.4 0 0 0 3.6.57 1 1 0 0 1 1 1V20a1 1 0 0 1-1 1A17 17 0 0 1 3 4a1 1 0 0 1 1-1h3.5a1 1 0 0 1 1 1c0 1.25.2 2.45.57 3.57a1 1 0 0 1-.25 1z"/></svg>
          <span>0431 286 517</span>
        </li>
        <li>
          <svg class="contact-icon" viewBox="0 0 24 24" aria-hidden="true"><rect x="2" y="5" width="20" height="14" rx="2" fill="#27a9e1"/><path d="M3 6l9 7 9-7" fill="none" stroke="#fff" stroke-width="2"/></svg>
          <span>rowan@tbk-plumbing.com.au</span>
        </li>
      </ul>
    </div>
  </section>

  <section class="card card-back" aria-label="Business card back">
    <div class="brand">
      <div class="brand-name">tbk</div>
      <div class="brand-tag">plumbing services</div>
    </div>
  </section>

</main>
</body>
</html>
```